Realty Group Needs Classy, Contemporary Letterhead Design

We need a letterhead design for a new realty company located in NY, USA. We buy investment properties to rehabilitate and or keep in our rental portfolio.

```html
<!DOCTYPE html>
<html lang="en">
<head>
<meta charset="utf-8">
<title>Halvorsen Realty Group — Letterhead</title>
<link rel="stylesheet" href="https://fonts.googleapis.com/css2?family=Open+Sans:wght@400;600;700&family=Homemade+Apple&display=swap">
<style>
  :root {
    --backdrop: #ecebed;
    --paper: #ffffff;
    --brand: #4a2a8f;
    --edge-grey: #9a9a9a;
    --ink: #4d4d4d;
    --ink-soft: #6a6a6a;
  }
  * { margin: 0; padding: 0; box-sizing: border-box; }
  html, body {
    width: 1200px; height: 795px; overflow: hidden;
    background: var(--backdrop);
    font-family: "Open Sans", Arial, sans-serif;
    color: var(--ink);
  }
  .letterhead {
    position: absolute; left: 335px; top: 22px;
    width: 530px; height: 750px;
    background: var(--paper);
    box-shadow: 0 2px 10px rgba(0,0,0,.08);
  }
  .edge-rule {
    position: absolute; right: 0; top: 0; width: 4px; height: 100%;
    background: var(--brand);
  }
  .edge-rule::before {
    content: ""; position: absolute; left: 0; top: 0; width: 4px; height: 58px;
    background: var(--edge-grey);
  }
  .brand-name {
    position: absolute; left: 40px; top: 48px;
    color: var(--brand); font-weight: 700; font-size: 19px; letter-spacing: .5px;
    display: flex; align-items: center; gap: 6px;
  }
  .brand-name .dot { width: 9px; height: 9px; border-radius: 50%; background: var(--brand); }
  .brand-sub {
    position: absolute; left: 56px; top: 72px;
    color: var(--brand); font-weight: 700; font-size: 6.5px; letter-spacing: 1px;
  }
  .contact {
    position: absolute; right: 40px; top: 34px;
    font-size: 7px; line-height: 11px; color: var(--ink);
  }
  .contact li { list-style: none; display: flex; align-items: center; gap: 4px; }
  .contact svg { width: 8px; height: 8px; fill: var(--brand); }
  .letter-body {
    position: absolute; left: 56px; top: 132px; width: 400px;
    font-size: 8.5px; line-height: 12px; color: var(--ink-soft);
  }
  .date { margin-bottom: 14px; }
  .recipient { margin-bottom: 14px; }
  .salutation { font-weight: 700; font-size: 10px; color: var(--ink); margin-bottom: 12px; }
  .letter-body p.para { margin-bottom: 14px; }
  .closing {
    position: absolute; right: 40px; top: 450px; width: 120px;
    font-size: 8.5px; line-height: 12px; color: var(--ink-soft);
  }
  .signature {
    font-family: "Homemade Apple", cursive; font-size: 16px; color: var(--ink);
    margin: 10px 0 6px;
  }
  .website {
    position: absolute; right: 40px; bottom: 36px;
    color: var(--brand); font-weight: 600; font-size: 9px;
  }
</style>
</head>
<body>
<main class="letterhead">
  <div class="edge-rule"></div>

  <div class="brand-name"><span>HALVORSEN</span><span class="dot"></span></div>
  <div class="brand-sub">Realty Group, LLC</div>

  <ul class="contact">
    <li>Suite 102 Street name,</li>
    <li>State, Zip 20234, Country</li>
    <li><svg viewBox="0 0 10 10"><path d="M2 1h2l1 2-1.2 1a5 5 0 0 0 2.2 2.2L7 5l2 1v2a1 1 0 0 1-1 1A7 7 0 0 1 1 2a1 1 0 0 1 1-1z"/></svg>000 01234 567 890</li>
    <li><svg viewBox="0 0 10 10"><path d="M2 1h2l1 2-1.2 1a5 5 0 0 0 2.2 2.2L7 5l2 1v2a1 1 0 0 1-1 1A7 7 0 0 1 1 2a1 1 0 0 1 1-1z"/></svg>000 01234 567 891</li>
    <li><svg viewBox="0 0 10 10"><circle cx="5" cy="5" r="4" fill="none" stroke="#4a2a8f" stroke-width="1.4"/><circle cx="5" cy="5" r="1.5"/></svg>hello@halvorsenrealty.com</li>
  </ul>

  <section class="letter-body">
    <p class="date">January 03, 2017</p>
    <p class="recipient">Mr. John Doe<br>President<br>AA Corporation<br>111 Street Name, Suite#<br>City, State, 12345</p>
    <p class="salutation">Dear Mr. John,</p>
    <p class="para">Lorem Ipsum is simply dummy text of the printing and typesetting industry. Lorem Ipsum has been the industry's standard dummy text ever since the 1500s, when an unknown printer took a galley of type and scrambled it to make a type specimen book. It has survived not only five centuries, but also the leap into electronic typesetting, remaining essentially unchanged.</p>
    <p class="para">The standard chunk of Lorem Ipsum used since the 1500s is reproduced below for those interested. Sections 1.10.32 and 1.10.33 from "de Finibus Bonorum et Malorum" by Cicero are also reproduced in their exact original form, accompanied by English versions from the 1914 translation by H. Rackham</p>
    <p class="para">Lorem Ipsum is simply dummy text of the printing and typesetting industry. Lorem Ipsum has been the industry's standard dummy text ever since the 1500s, when an unknown printer took a galley of type and scrambled it to make a type specimen book. It has survived not only five centuries, but also the leap into electronic typesetting, remaining essentially unchanged. It was popularised in the</p>
  </section>

  <div class="closing">
    <p>Sincerely Your,</p>
    <p class="signature">your name</p>
    <p>Name Last Name<br>Company Name</p>
  </div>

  <p class="website">www.halvorsenrealtygroup.com</p>
</main>
</body>
</html>
```